Storefront signage for Physio clinic

We need a design for our storefront windows at our physiotherapy & Pilates clinic.

The design should be modern and include our logo, website url and services (physiotherapy, pilates, massage).

Some inspirational exercise/pilates/recovery quotes may be included and I would like to see the use of sport/pilates/injury related stock images. I have attached a few examples of what we want (images numbered 1-5). And I have attached our current design and photo of the outside of our clinic.

In the attached images there is also a pdf with measurments of our window panels. We require signage for the areas marked 1-10. As you can see on our current signage, you don't need to have a separate image for each panel, these can flow onto each other.
Updates

Industry/Entity Type

Clinic

Colors
85acd3
3377b5
3277b5
e8e8e8
c3c3c3
9d9d9d
848484
7f7f7f

Requirements
Must have
• Stock images related to sports, physiotherapy and pilates
• Ideally these images should be in greyscale and blend in with the rest of the panel which should include colours.
• I would like to see for example a runner, a weightlifter, someone doing pilates, someone with back pain (not necessarily all of these).
Should not have
• I want a creative, modern, up market design, not just a standard recycled template.

```html
<!DOCTYPE html>
<html lang="en">
<head>
<meta charset="utf-8">
<title>Harbourside Physio &amp; Pilates – Window Signage</title>
<link href="https://fonts.googleapis.com/css2?family=Montserrat:wght@400;600;800&display=swap" rel="stylesheet">
<style>
  :root{
    --blue-light:#85acd3;
    --blue:#3377b5;
    --blue-mid:#4a7fc2;
    --blue-deep:#1e4a86;
    --cyan:#1aa3d9;
    --grey-100:#e8e8e8;
    --grey-300:#c3c3c3;
    --grey-500:#9d9d9d;
    --grey-700:#7f7f7f;
    --grey-900:#3a3a3a;
    --white:#ffffff;
    --bg:#eef0f2;
  }
  *{box-sizing:border-box;margin:0;padding:0}
  html,body{width:1200px;height:770px;overflow:hidden;background:var(--bg);font-family:"Montserrat",sans-serif}
  .signage{position:relative;width:1200px;height:770px}
  .panel{position:absolute;overflow:hidden;box-shadow:0 6px 20px rgba(0,0,0,.12)}
  .panel--good-things{left:22px;top:247px;width:385px;height:273px}
  .panel--push-harder{left:467px;top:255px;width:345px;height:265px}
  .panel--door-left{left:862px;top:261px;width:101px;height:259px;background:var(--blue-deep)}
  .panel--door-right{left:1077px;top:261px;width:101px;height:259px;background:var(--blue-mid)}
  .photo{position:absolute;inset:0}
  .photo--hands{background:linear-gradient(115deg,var(--grey-100) 0%,var(--grey-300) 35%,var(--grey-700) 65%,var(--grey-900) 100%)}
  .photo--pilates{background:linear-gradient(90deg,var(--grey-300) 0%,var(--white) 30%,var(--grey-100) 60%,var(--grey-500) 100%)}
  .photo--cross{inset:auto;background:linear-gradient(160deg,var(--grey-100),var(--grey-700));
    clip-path:polygon(0 20%,20% 0,50% 30%,80% 0,100% 20%,70% 50%,100% 80%,80% 100%,50% 70%,20% 100%,0 80%,30% 50%)}
  .overlay{position:absolute;inset:0;width:100%;height:100%}
  .brand{position:absolute;display:flex;align-items:center;gap:3px;color:var(--blue);font-weight:800;font-size:6px;letter-spacing:.3px;text-transform:uppercase;white-space:nowrap}
  .brand__dot{width:9px;height:9px;border-radius:50%;background:var(--blue)}
  .headline{position:absolute;color:var(--blue-deep);font-weight:800;font-size:17px;line-height:1}
  .tagline{position:absolute;color:var(--blue);font-size:5.5px;font-weight:600;white-space:nowrap}
  .cta{position:absolute;background:var(--blue-deep);color:var(--white);font-size:4.5px;font-weight:800;height:9px;line-height:9px;text-align:center;letter-spacing:.4px}
  .services{position:absolute;display:flex;gap:3px}
  .services span{background:var(--blue);color:var(--white);font-size:4.5px;font-weight:600;height:8px;line-height:8px;padding:0 4px;letter-spacing:.3px;flex:1;white-space:nowrap;overflow:hidden}
  .services span:first-child{background:var(--blue-light)}
  .url{position:absolute;font-size:5px;font-weight:600;white-space:nowrap}
  .door-text{position:absolute;left:6px;right:6px;color:var(--white);font-size:4.5px;font-weight:600;line-height:1.4}
</style>
</head>
<body>
<main class="signage">

  <section class="panel panel--good-things">
    <div class="photo photo--hands" role="img" aria-label="Greyscale photo of an athlete's hands gripping a knee"></div>
    <svg class="overlay" viewBox="0 0 385 273" aria-hidden="true">
      <polygon points="0,0 150,0 0,140" fill="var(--blue)"/>
      <polygon points="150,0 200,0 0,190 0,140" fill="var(--cyan)"/>
      <g transform="translate(0,20)">
        <polygon points="0,34 34,0 85,51 136,0 170,34 119,85 170,136 136,170 85,119 34,170 0,136 51,85" fill="var(--white)"/>
        <rect x="32" y="42" width="106" height="86" fill="var(--white)"/>
      </g>
    </svg>
    <div class="brand" style="top:30px;right:14px"><span class="brand__dot"></span>Harbourside Physio</div>
    <div class="headline" style="left:40px;top:69px">GOOD<br>THINGS</div>
    <div class="tagline" style="left:40px;top:106px">come to those who sweat...</div>
    <div class="cta" style="left:40px;top:126px;width:86px">ENROLL NOW!</div>
    <div class="services" style="left:38px;right:41px;top:222px">
      <span>PHYSIOTHERAPY</span><span>PILATES</span><span>MASSAGE</span><span>WORK REHABILITATION</span>
    </div>
    <div class="url" style="left:180px;top:258px;color:var(--grey-100)">harbourphysio.com.au</div>
  </section>

  <section class="panel panel--push-harder">
    <div class="photo photo--pilates" role="img" aria-label="Greyscale photo of a woman doing a Pilates stretch over an exercise ball"></div>
    <svg class="overlay" viewBox="0 0 345 265" aria-hidden="true">
      <polygon points="345,80 345,265 205,265" fill="var(--cyan)"/>
      <g transform="translate(186,82)">
        <polygon points="0,34 34,0 85,51 136,0 170,34 119,85 170,136 136,170 85,119 34,170 0,136 51,85" fill="var(--white)"/>
        <rect x="34" y="42" width="106" height="86" fill="var(--white)"/>
      </g>
      <rect x="0" y="260" width="345" height="5" fill="var(--blue-deep)"/>
    </svg>
    <div class="services" style="left:22px;right:6px;top:47px">
      <span>PHYSIOTHERAPY</span><span>PILATES</span><span>MASSAGE</span><span>WORK REHABILITATION</span>
    </div>
    <div class="brand" style="top:30px;right:12px"><span class="brand__dot"></span>Harbourside Physio</div>
    <div class="headline" style="left:232px;top:148px">PUSH<br>HARDER</div>
    <div class="tagline" style="left:232px;top:184px">for a different tomorrow...</div>
    <div class="cta" style="left:232px;top:195px;width:75px">ENROLL NOW!</div>
    <div class="url" style="left:144px;top:250px;color:var(--grey-700)">harbourphysio.com.au</div>
  </section>

  <section class="panel panel--door-left">
    <div class="photo photo--cross" role="img" aria-label="Greyscale photo of a woman holding a Pilates pose, cropped in a cross shape"
         style="left:4px;top:75px;width:92px;height:100px"></div>
    <div class="door-text" style="top:236px">02 9000 1234</div>
  </section>

  <section class="panel panel--door-right">
    <div class="photo photo--cross" role="img" aria-label="Greyscale photo of a person with shoulder pain highlighted in red, cropped in a cross shape"
         style="left:4px;top:80px;width:92px;height:100px"></div>
    <div class="door-text" style="top:226px;text-align:center">Shop 3, 12 Harbour St<br>Rockdale NSW<br>harbourphysio.com.au</div>
  </section>

</main>
</body>
</html>
```